Business Card Re-Design/Update

We'd like to update out business cards. I've included our current "Style guide" which has the colour scheme of the organisation in it. I've also included the branding files with logos etc in them.

I've also included a copy of one of our existing cards so that you can see how ugly/dated they look. I'd like a fresh modern corporate look.

Target Market(s)

These are for our clients, potential clients, industry contacts - like all business cards

Contact Information for Business Card

Name
Position
Company Address - Level 1, 47 Fernby Street, Carlow Qld 4072
Direct Phone
mobile
Email
Website -www.korvalit.com.au
Logo

Colors

Designer to choose colors to be used in the design.

Requirements
Must have
• Main Logo
• Cards will need to be editable to be able to personalize them for each new employee.
Nice to have
• The MapOut, ShipWell, KeepSteady would be okay to have if they can be sensibly and professionally added to the look without detracting from the main imagery.
• Maybe they could go on the back of the card? will leave this to your creative discretion as to whether/where they fit.
Should not have
• Should not have decorative or script fonts

```html
<!DOCTYPE html>
<html lang="en">
<head>
<meta charset="utf-8">
<title>korvalIT business card</title>
<link rel="stylesheet" href="https://fonts.googleapis.com/css2?family=Roboto:wght@400;500;700&family=Roboto+Condensed:wght@700&display=swap">
<style>
  :root {
    --backdrop: #2a2a2a;
    --brand-red: #c8161d;
    --brand-red-light: #d81e26;
    --card-white: #f2f2f2;
    --ink: #231f20;
    --white: #ffffff;
    --map-green: #5a9a3a;
    --ship-blue: #1b8ad3;
    --keep-magenta: #b5268f;
  }
  html, body {
    margin: 0;
    padding: 0;
    width: 1200px;
    height: 960px;
    overflow: hidden;
    background: var(--backdrop);
    font-family: "Roboto", Arial, sans-serif;
  }
  .canvas {
    position: relative;
    width: 1200px;
    height: 960px;
  }
  .card {
    position: absolute;
    width: 598px;
    height: 342px;
    box-sizing: border-box;
  }
  .card-front {
    left: 322px;
    top: 108px;
    background: radial-gradient(circle at 75% 40%, var(--brand-red-light), var(--brand-red) 70%);
    color: var(--white);
  }
  .card-back {
    left: 320px;
    top: 493px;
    background: var(--card-white);
  }
  .brand {
    position: absolute;
    display: flex;
    align-items: center;
  }
  .brand-square {
    display: block;
    background: currentColor;
  }
  .front-brand {
    left: 36px;
    top: 34px;
    color: var(--white);
    gap: 12px;
  }
  .front-brand .brand-square { width: 34px; height: 34px; }
  .front-brand .brand-name {
    font-weight: 700;
    font-size: 31px;
    letter-spacing: -0.5px;
  }
  .holder-name {
    position: absolute;
    left: 33px;
    top: 107px;
    margin: 0;
    font-family: "Roboto Condensed", "Arial Narrow", sans-serif;
    font-weight: 700;
    font-size: 21px;
  }
  .holder-role {
    position: absolute;
    left: 33px;
    top: 133px;
    margin: 0;
    font-size: 14px;
  }
  .address {
    position: absolute;
    left: 33px;
    top: 163px;
    margin: 0;
    font-style: normal;
    font-size: 14px;
    line-height: 18px;
  }
  .contact-list {
    position: absolute;
    left: 33px;
    top: 207px;
    margin: 0;
    padding: 0;
    list-style: none;
    font-size: 14px;
    line-height: 19px;
  }
  .contact-list li {
    display: flex;
    align-items: center;
    gap: 9px;
  }
  .contact-list svg {
    width: 13px;
    height: 13px;
    fill: var(--white);
  }
  .back-brand {
    left: 94px;
    top: 118px;
    color: var(--ink);
    gap: 16px;
  }
  .back-brand .brand-square { width: 62px; height: 62px; color: var(--brand-red); }
  .back-brand .brand-name {
    font-weight: 500;
    font-size: 50px;
    letter-spacing: -1px;
  }
  .service-row {
    position: absolute;
    left: 48px;
    top: 275px;
    display: flex;
    gap: 36px;
  }
  .service {
    display: flex;
    align-items: center;
    gap: 7px;
    font-weight: 500;
    font-size: 26px;
    letter-spacing: -0.5px;
  }
  .service .brand-square { width: 24px; height: 24px; }
  .service-map { color: var(--map-green); }
  .service-ship { color: var(--ship-blue); }
  .service-keep { color: var(--keep-magenta); }
</style>
</head>
<body>
<main class="canvas">
  <section class="card card-front" aria-label="Card front">
    <div class="brand front-brand">
      <span class="brand-square"></span>
      <span class="brand-name">korvalIT</span>
    </div>
    <h1 class="holder-name">DANA WHITFIELD</h1>
    <p class="holder-role">Business Development Manager</p>
    <address class="address">Level 1, 47 Fernby Street<br>Carlow Qld 4072</address>
    <ul class="contact-list">
      <li><svg viewBox="0 0 16 16" aria-hidden="true"><path d="M3.5 1l3 3-1.8 2a9 9 0 0 0 5.3 5.3l2-1.8 3 3-2 2C6.5 14 2 9.5 1.5 3z"/></svg>+61 (0)7 5550 1420</li>
      <li><svg viewBox="0 0 16 16" aria-hidden="true"><path d="M3.5 1l3 3-1.8 2a9 9 0 0 0 5.3 5.3l2-1.8 3 3-2 2C6.5 14 2 9.5 1.5 3z"/></svg>+61 (0)7 5550 1436</li>
      <li><svg viewBox="0 0 16 16" aria-hidden="true"><path d="M4 0h8a1 1 0 0 1 1 1v14a1 1 0 0 1-1 1H4a1 1 0 0 1-1-1V1a1 1 0 0 1 1-1zm1 2v10h6V2zm3 11a1 1 0 1 0 0 2 1 1 0 0 0 0-2z"/></svg>+61 (0)400 555 718</li>
      <li><svg viewBox="0 0 16 16" aria-hidden="true"><path d="M4 1h8v4H4zM1 6h14v6h-2v-2H3v2H1zm3 5h8v4H4z"/></svg>+61 (0)7 5550 1499</li>
      <li><svg viewBox="0 0 16 16" aria-hidden="true"><path d="M1 3h14v10H1zm1.5 1.5v.4L8 9l5.5-4.1v-.4z"/></svg>dwhitfield@korvalit.com.au</li>
      <li><svg viewBox="0 0 16 16" aria-hidden="true"><path d="M8 1a7 7 0 1 0 0 14A7 7 0 0 0 8 1zm0 1.5c.9 0 1.9 1.6 2.2 4H5.8C6.1 4.1 7.1 2.5 8 2.5zM5.8 9.5h4.4c-.3 2.4-1.3 4-2.2 4s-1.9-1.6-2.2-4z"/></svg>www.korvalit.com.au</li>
    </ul>
  </section>

  <section class="card card-back" aria-label="Card back">
    <div class="brand back-brand">
      <span class="brand-square"></span>
      <span class="brand-name">korvalIT</span>
    </div>
    <div class="service-row">
      <span class="service service-map"><span class="brand-square"></span>MapOut</span>
      <span class="service service-ship"><span class="brand-square"></span>ShipWell</span>
      <span class="service service-keep"><span class="brand-square"></span>KeepSteady</span>
    </div>
  </section>
</main>
</body>
</html>
```